New design for existing catalog pages

We want to update and improve our existing design. The existing products on the designs should be adopted. Also the prices, descriptions and article numbers.
It is important that we receive an Indesign file that we can adapt. Also replace the images and adjust texts and prices.

Target Market(s)

Older people with high incomes. More conservative people.

Industry/Entity Type

Münzen und Briefmarkenhandel

Requirements
Must have
• Noble, simple and timeless design that looks high quality.
Nice to have
• The expensive products should be presented accordingly
Should not have
• Don't look cheap. Not too many different and bright colors

```html
<!DOCTYPE html>
<html lang="de">
<head>
<meta charset="utf-8">
<title>Katalogseiten Goldmünzen</title>
<link href="https://fonts.googleapis.com/css2?family=Cabin:wght@400;500;600;700&family=Cabin+Condensed:wght@600;700&display=swap" rel="stylesheet">
<style>
  :root{
    --navy:#0f2256;
    --navy-deep:#0a1a45;
    --panel:#e1e3e7;
    --paper:#ffffff;
    --backdrop:#ebebeb;
    --ink:#1b1b1f;
    --rule:#9aa0ab;
    --ribbon:#1d4f9c;
    --ribbon-dark:#0e2f6c;
    --gold-light:#f4dc8c;
    --gold:#d6aa3c;
    --gold-dark:#9c7418;
  }
  *{box-sizing:border-box;margin:0;padding:0}
  html,body{width:1200px;height:2487px;overflow:hidden}
  body{background:var(--backdrop);font-family:"Cabin",sans-serif;color:var(--ink);position:relative}
  .page{position:absolute;left:179px;width:842px;background:var(--paper);box-shadow:0 0 12px rgba(0,0,0,.18)}
  .page--one{top:72px;height:1151px}
  .page--two{top:1258px;height:1151px}

  .offer{position:absolute;left:38px;width:766px;background:var(--panel);overflow:hidden}
  .offer__title{position:absolute;left:0;top:0;width:100%;height:50px;background:var(--navy);color:#fff;
    font-family:"Cabin",sans-serif;font-weight:600;font-size:29px;letter-spacing:.3px;text-align:center;line-height:50px}
  .offer__wedge{position:absolute;left:0;top:50px;width:100%}
  .coin{position:absolute;border-radius:50%;
    background:radial-gradient(circle at 38% 34%,var(--gold-light) 0%,var(--gold) 55%,var(--gold-dark) 100%);
    box-shadow:3px 4px 10px rgba(0,0,0,.35)}
  .offer__text{position:absolute;left:19px;font-size:12.4px;line-height:16.4px}
  .offer__text p{margin-bottom:4px}
  .offer__text--wrap{font-size:12px;line-height:16px}
  .coin-wrap{float:right;width:70px;height:200px;shape-outside:circle(131px at 138px 137px)}
  .specs{position:absolute;left:19px;background:#fff;padding:6px 8px}
  .specs ul{list-style:none;border:1px solid var(--rule);padding:5px 8px;height:100%}
  .specs li{font-size:11px;line-height:15px;padding-left:14px;position:relative}
  .specs li::before{content:"›";position:absolute;left:2px;top:-1px;font-size:14px;color:#555}
  .sku{position:absolute;left:20px;font-family:"Cabin Condensed",sans-serif;font-weight:700;font-size:20px;letter-spacing:.3px}
  .ribbon{position:absolute;height:38px;color:#fff;font-family:"Cabin Condensed",sans-serif;font-weight:700;
    font-size:20px;text-align:center;line-height:38px;
    background:linear-gradient(180deg,#3f74c0 0%,var(--ribbon) 45%,var(--ribbon-dark) 100%);
    clip-path:polygon(0 12%,8% 0,8% 10%,92% 10%,92% 0,100% 12%,100% 100%,0 100%)}

  .intro{position:absolute;left:22px;top:64px;width:723px;font-size:13.8px;line-height:18.4px;text-align:justify}
  .intro p{margin-bottom:8px}
  .band{position:absolute;left:0;top:795px;width:100%;height:163px;background:var(--navy)}
  .checks{position:absolute;left:497px;top:846px;width:251px;height:139px;background:#fff;padding:9px 12px}
  .checks ul{list-style:none;border:1px solid var(--rule);height:100%;padding:6px 10px}
  .checks li{font-size:11px;line-height:19px;display:flex;align-items:center;gap:7px}
  .checks svg{flex:none}
  .price-row{position:absolute;left:20px;width:726px;display:flex;font-family:"Cabin Condensed",sans-serif;
    font-weight:700;font-size:20px;letter-spacing:.2px}
  .price-row .num{width:150px}
  .price-row .name{flex:1}
  .price-rule{position:absolute;left:20px;width:726px;height:1px;background:var(--rule)}
</style>
</head>
<body>

<section class="page page--one">
  <article class="offer" style="top:43px;height:349px">
    <h2 class="offer__title">20 Franken 1873, 3-Punkt - Probeprägung</h2>
    <svg class="offer__wedge" width="766" height="299" viewBox="0 0 766 299" aria-hidden="true">
      <polygon points="560,0 766,0 766,299 370,299" fill="var(--navy)"/>
    </svg>
    <div class="offer__text offer__text--wrap" style="top:62px;width:290px">
      <div class="coin-wrap" aria-hidden="true"></div>
      <p>1873 liess das Finanzdepartement vom bekannten Graveur Leon Weidmann in seiner Prägestätte in Brüssel ein Stempelpaar und 1‘000 Exemplare einer neuen Eidgenössischen Goldmünze anfertigen. Der oberste der drei Punkte beinhaltete das Münzzeichen des Graveurs und stellte einen Engelskopf dar, der jedoch bei oberflächlicher Betrachtung als Punkt wahrgenommen wird.</p>
    </div>
    <div class="specs" style="top:222px;width:210px;height:90px">
      <ul>
        <li>Jahr 1873</li>
        <li>Gold – 900/1‘000 Feinheit</li>
        <li>Gewicht 6,451 Gramm</li>
        <li>Durchmesser 21mm</li>
        <li>Auflage: 1‘000 Stück</li>
      </ul>
    </div>
    <div class="sku" style="top:316px">7870.1873.01</div>
    <div class="sku" style="top:316px;left:202px">9995,– CHF</div>
    <div class="coin" role="img" aria-label="Münzfoto: Wertseite 20 Fr. 1873 im Lorbeerkranz" style="left:252px;top:74px;width:250px;height:250px"></div>
    <div class="coin" role="img" aria-label="Münzfoto: Bildseite mit sitzender Helvetia und Schweizer Wappenschild" style="left:492px;top:66px;width:266px;height:266px"></div>
  </article>

  <article class="offer" style="top:403px;height:348px">
    <h2 class="offer__title">Das 100 Franken Vreneli von 1925</h2>
    <svg class="offer__wedge" width="766" height="298" viewBox="0 0 766 298" aria-hidden="true">
      <polygon points="560,0 766,0 766,298 370,298" fill="var(--navy)"/>
    </svg>
    <div class="ribbon" style="left:18px;top:78px;width:180px">Top - Rarität</div>
    <div class="offer__text" style="top:123px;width:180px">
      <p>1925, 100 Fr. Gold-Vreneli, bis unzirkuliert, mit Stempelglanz, Top-Erhaltung,</p>
      <p>Durchmesser: 35mm,</p>
      <p>Motiv: Helvetiakopf (Vreneli),</p>
      <p>Entwurf: Franz Ulrich Lanz, Neuchâtel, Münzzeichen B,</p>
      <p>Auflage: 5‘000</p>
    </div>
    <div class="sku" style="top:285px">7874.1925.08</div>
    <div class="sku" style="top:316px">25900,– CHF</div>
    <div class="coin" role="img" aria-label="Münzfoto: Wertseite 100 FR 1925 mit Schweizerkreuz im Strahlenkranz" style="left:210px;top:61px;width:274px;height:274px"></div>
    <div class="coin" role="img" aria-label="Münzfoto: Bildseite Helvetiakopf mit Schriftzug HELVETIA" style="left:477px;top:58px;width:280px;height:280px"></div>
  </article>

  <article class="offer" style="top:763px;height:349px">
    <h2 class="offer__title">Das 100 Franken Vreneli von 1925</h2>
    <svg class="offer__wedge" width="766" height="299" viewBox="0 0 766 299" aria-hidden="true">
      <polygon points="560,0 766,0 766,299 370,299" fill="var(--navy)"/>
    </svg>
    <div class="ribbon" style="left:21px;top:78px;width:180px">Top - Qualität</div>
    <div class="offer__text" style="top:123px;width:180px">
      <p>1925, 100 Fr. Gold-Vreneli, fast FDC, Top-Erhaltung,</p>
      <p>Durchmesser:35mm, Motiv: Helvetiakopf (Vreneli),</p>
      <p>Entwurf: Franz Ulrich Lanz, Neuchâtel, Münzzeichen B,</p>
      <p>Auflage: 5‘000</p>
    </div>
    <div class="sku" style="top:284px">7874.1925.07</div>
    <div class="sku" style="top:316px">25900,– CHF</div>
    <div class="coin" role="img" aria-label="Münzfoto: Wertseite 100 FR 1925 mit Schweizerkreuz im Strahlenkranz" style="left:210px;top:61px;width:274px;height:274px"></div>
    <div class="coin" role="img" aria-label="Münzfoto: Bildseite Helvetiakopf vor Bergkulisse" style="left:479px;top:58px;width:282px;height:282px"></div>
  </article>
</section>

<section class="page page--two">
  <article class="offer" style="top:44px;height:1068px">
    <h2 class="offer__title" style="height:57px;line-height:57px;font-size:25px">Duplone und Doppelduplone der Helvetischen Republik 1798 - 1803</h2>
    <div class="intro">
      <p>Helvetische Republik ist die offizielle Bezeichnung des schweizerischen Staatswesens, das am 12. April 1798 die alte Eidgenossenschaft ablöste und bis zum 10. März 1803 bestand.</p>
      <p>Frankreich nutzte die bestehende Unzufriedenheit der ländlichen Eliten in den Untertanengebieten der alten Eidgenossenschaft, sowie der aufgeklärten Bürger in den städtischen Orten und förderte gezielt re-volutionäre Bestrebungen. Angefacht oder ausgelöst und zugleich auch abgesichert wurde die Umwälzung durch französische Truppen, die ab Ende Januar in einer Zangenbewegung von der Waadt und vom Jura her in das westliche Mittelland vorstiessen (Franzoseneinfall). In den Kampfhandlungen Anfang März 1798 ging die alte Eidgenossenschaft unter.</p>
      <p>Einige Städte, allen voran Bern, hatten beträchtliche Vermögen in ihren Schatzkammern. Der sogenannte Staatsschatz von Bern wurde von den Französischen Truppen geplündert. Mehrere Kutschen mit Gold und Silber, sowie die Bären aus dem Bärengraben, wurden nach Paris gekarrt.</p>
      <p>Mit der Einführung der Helvetischen Republik ging das Münzwesen von den Kantonen auf den Zentralstaat über und der Franken wurde als Währung festgelegt. In dieser Zeit entstanden die Duplonen (16 Franken) und Doppelduplonen (32 Franken) der Helvetischen Republik.</p>
    </div>
    <div class="band"></div>
    <div class="coin" role="img" aria-label="Münzfoto: Bildseite mit Fahnenträger, Umschrift Helvetische Republik" style="left:257px;top:320px;width:358px;height:358px"></div>
    <div class="coin" role="img" aria-label="Münzfoto: Wertseite 32 Franken 1800 im Kranz" style="left:19px;top:547px;width:400px;height:400px"></div>
    <div class="coin" role="img" aria-label="Münzfoto: Wertseite 16 Franken 1800 im Kranz" style="left:475px;top:569px;width:250px;height:250px"></div>
    <div class="ribbon" style="left:97px;top:371px;width:242px;height:52px;line-height:52px;font-size:23px">TOP - RARITÄT</div>
    <div class="ribbon" style="left:352px;top:782px;width:239px;height:50px;line-height:50px;font-size:22px">DUPLONENPAAR</div>
    <div class="checks">
      <ul>
        <li><svg width="11" height="10" viewBox="0 0 11 10"><path d="M1 5l3 3 6-7" fill="none" stroke="var(--ribbon)" stroke-width="2"/></svg>Schweiz - 16 / 32 Franken</li>
        <li><svg width="11" height="10" viewBox="0 0 11 10"><path d="M1 5l3 3 6-7" fill="none" stroke="var(--ribbon)" stroke-width="2"/></svg>1800, Helvetische Republik</li>
        <li><svg width="11" height="10" viewBox="0 0 11 10"><path d="M1 5l3 3 6-7" fill="none" stroke="var(--ribbon)" stroke-width="2"/></svg>7,65 Gramm / 15,26 Gramm - Gold</li>
        <li><svg width="11" height="10" viewBox="0 0 11 10"><path d="M1 5l3 3 6-7" fill="none" stroke="var(--ribbon)" stroke-width="2"/></svg>23 mm / 29 mm Durchmesser</li>
        <li><svg width="11" height="10" viewBox="0 0 11 10"><path d="M1 5l3 3 6-7" fill="none" stroke="var(--ribbon)" stroke-width="2"/></svg>vorzüglich bis unzirkuliert</li>
      </ul>
    </div>
    <div class="price-row" style="top:994px">
      <span class="num">7997.1800.015</span><span class="name">Helvetische Republik - Duplone 16 Franken</span><span>9500,– CHF</span>
    </div>
    <div class="price-rule" style="top:1024px"></div>
    <div class="price-row" style="top:1031px">
      <span class="num">7997.1800.025</span><span class="name">Helvetische Republik - Doppelduplone 32 Franken</span><span>28900,– CHF</span>
    </div>
  </article>
</section>

</body>
</html>
```